New Electrical Contractor looking for local work

I have just started working for myself as an Electrical Contractor, based in the eastern suburbs of Melbourne. I want to advertise in the local area so hopefully I can create a client base that is close to home, so I thought a flyer that I could drop in letterboxes could be a good start. Most of my experience has been domestic houses, so ideally this is the work I would like to get more of.

Here is a list of the work I usually do:
Extensions / Renovations
Safety Switch and Switchboard Upgrades
LED Lighting including downlights/light fittings and LED strip light
Re-wires
Maintenance

I have also added a couple of images of LED strip lights and how they can be used in homes. There are a lot more on google images if anyone thinks they could be of use.

These are my details:
Business name - Dirk Malan Electrical
Phone - 0437 218 064
ABN - 41 382 704 916
REC - 58317
Email - malanelectrical@brivomail.net

I will attach my business logo and business card
Updates

Could I please ask for all designs to delete the "(contractors registration number)" text.

Only REC 58317 needs to be displayed.

Thank you kindly

Industry/Entity Type

Business

Requirements
Must have
• My contact details, ie. Name, Phone, email, ABN, REC etc

```html
<!DOCTYPE html>
<html lang="en">
<head>
<meta charset="utf-8">
<title>Dirk Malan Electrical – Flyer</title>
<link rel="stylesheet" href="https://fonts.googleapis.com/css2?family=Arimo:wght@400;700&family=Kalam:wght@700&family=Roboto+Condensed:wght@400;700&display=swap">
<style>
  :root {
    --backdrop: #c2b49c;
    --brown-deep: #5e2410;
    --brown: #8a3a1a;
    --brown-warm: #a8491f;
    --gold-light: #f6efc6;
    --gold: #e3d395;
    --gold-edge: #b89a4e;
    --ink: #3a3a3a;
    --panel: #e6e6e6;
    --tab: #1f1f1f;
    --service-red: #b0403a;
    --white: #ffffff;
  }
  * { margin: 0; padding: 0; box-sizing: border-box; }
  html, body { width: 935px; height: 1200px; overflow: hidden; }
  body { background: var(--backdrop); position: relative; font-family: "Arimo", Arial, sans-serif; }

  .flyer {
    position: absolute; left: 107px; top: 117px; width: 728px; height: 1014px;
    background: linear-gradient(180deg, var(--brown-deep) 0%, var(--brown) 45%, var(--brown-warm) 100%);
    box-shadow: 2px 3px 6px rgba(0,0,0,.35);
    overflow: hidden;
  }

  .hero-photo {
    position: absolute; left: 0; top: 160px; width: 728px; height: 420px;
    background:
      linear-gradient(180deg, rgba(138,58,26,0) 60%, var(--brown) 100%),
      radial-gradient(ellipse at 45% 55%, #e0a75c 0%, #9c5a28 30%, #4a2210 70%, #2a140a 100%);
  }

  .title-band {
    position: absolute; left: 6px; top: 36px; width: 717px; height: 147px;
    background: linear-gradient(180deg, var(--gold-light) 0%, var(--gold) 55%, #d2bd78 100%);
    border-top: 3px solid var(--gold-edge);
    border-bottom: 3px solid var(--gold-edge);
    border-radius: 10px;
    box-shadow: 0 3px 6px rgba(0,0,0,.35);
    overflow: hidden;
  }
  .brand-mark {
    position: absolute; left: 52px; top: 38px; width: 58px; height: 58px;
    border-radius: 50%; background: var(--ink);
  }
  .brand-name {
    position: absolute; left: 148px; top: 38px;
    font-family: "Roboto Condensed", "Arial Narrow", sans-serif; font-weight: 700;
    font-size: 50px; line-height: 1; color: var(--ink); white-space: nowrap;
  }
  .brand-tagline {
    position: absolute; left: 150px; top: 100px;
    font-size: 19px; letter-spacing: 3.5px; color: var(--ink);
  }

  .contact {
    position: absolute; right: 66px; top: 370px; text-align: right; color: var(--white);
    font-family: "Roboto Condensed", "Arial Narrow", sans-serif;
    text-shadow: 0 1px 3px rgba(0,0,0,.5);
  }
  .contact-label { font-size: 40px; line-height: 1; }
  .contact-phone { font-size: 50px; font-weight: 700; line-height: 1.05; }

  .services-panel {
    position: absolute; left: 45px; top: 499px; width: 627px; height: 422px;
    background: var(--panel); box-shadow: 0 2px 6px rgba(0,0,0,.35);
  }
  .services-tab {
    position: absolute; left: 31px; top: -6px; width: 428px; height: 63px;
    background: linear-gradient(180deg, #3d3d3d, var(--tab)); border-radius: 7px;
    color: var(--white); font-family: "Kalam", cursive; font-weight: 700; font-size: 36px; line-height: 66px;
    padding-left: 50px; letter-spacing: 1px;
  }
  .corner-ribbon { position: absolute; right: -4px; top: -10px; width: 160px; height: 160px; }

  .service-list { position: absolute; left: 18px; top: 72px; list-style: none; }
  .service-list li {
    position: relative; padding-left: 62px; color: var(--service-red);
    font-family: "Kalam", cursive; font-weight: 700; font-size: 25px; line-height: 38px;
  }
  .service-num {
    position: absolute; left: 0; top: 7px; width: 42px; height: 24px;
    background: var(--tab); color: var(--white); font-family: "Arimo", sans-serif;
    font-size: 15px; font-weight: 700; line-height: 24px; text-align: center;
    clip-path: polygon(0 0, 80% 0, 100% 50%, 80% 100%, 0 100%);
    border-radius: 3px 0 0 3px;
  }

  .photo-strip {
    position: absolute; left: 0; bottom: 0; width: 627px; height: 70px;
    background: linear-gradient(90deg, #d8cfc4 0%, #9a7a5a 20%, #2e2c30 35%, #6e4a38 50%, #3d6c8c 65%, #b44a3a 80%, #e4ddd4 100%);
  }

  .email {
    position: absolute; left: 0; width: 728px; top: 938px; text-align: center;
    color: var(--white); font-size: 25px;
  }
  .email strong { font-weight: 700; }
  .registration {
    position: absolute; left: 0; width: 728px; top: 981px; text-align: center;
    color: var(--white); font-size: 13.5px; font-weight: 700; word-spacing: 2px;
  }
</style>
</head>
<body>
  <main class="flyer">
    <div class="hero-photo" role="img" aria-label="Photo of a warmly lit kitchen with timber cabinets and LED strip lighting under the bench"></div>

    <header class="title-band">
      <span class="brand-mark"></span>
      <h1 class="brand-name">DIRK MALAN ELECTRICAL</h1>
      <p class="brand-tagline">A GRADE ELECTRICIAN</p>
    </header>

    <div class="contact">
      <p class="contact-label">CONTACT</p>
      <p class="contact-phone">0437 218 064</p>
    </div>

    <section class="services-panel">
      <h2 class="services-tab">Services Includes</h2>
      <svg class="corner-ribbon" viewBox="0 0 160 160" aria-hidden="true">
        <polygon points="24,0 64,0 160,96 160,136" fill="#1f1f1f"/>
        <text transform="translate(100,62) rotate(45)" fill="#fff" font-family="Arimo, sans-serif" font-size="9" font-weight="700" letter-spacing="1.5" text-anchor="middle">A GRADE ELECTRICIAN</text>
      </svg>

      <ul class="service-list">
        <li><span class="service-num">1</span>Extensions / Renovations</li>
        <li><span class="service-num">2</span>Renovations</li>
        <li><span class="service-num">3</span>Re-wires</li>
        <li><span class="service-num">4</span>Maintenance</li>
        <li><span class="service-num">5</span>Safety Switch and Switchboard Upgrades</li>
        <li>LED Lighting including downlights/</li>
        <li>light fittings and LED strip light</li>
      </ul>

      <div class="photo-strip" role="img" aria-label="Row of photos of electrical work: cables, LED strip reel, testing tools, switchboard wiring and pliers"></div>
    </section>

    <p class="email">Email: <strong>malanelectrical@brivomail.net</strong></p>
    <p class="registration">ABN - 41 382 704 916 &nbsp;&nbsp; REC - 58317</p>
  </main>
</body>
</html>
```